Bright Harbor Counseling Letterhead for hip modern business

I would like some ombre use of the colors in the logo hip letterhead that incorporates logo colors and feel, needs to connect with young professionals and college students. i need to be able to write letters to schools to excuse absences as well. i like color blocks on one side preferably using colors from the attached logo design.

Target Market(s)

high income young people, young adults and college students

Industry/Entity Type

mental health

Font styles to use
Serif
Sans Serif

Colors
0054AA
0677BA
7BADD7
CADEEF
E8F1F8
0094D4
00A9DD
6FCCEA
C7EBF8
E9F6FB
00AB8E
00BBA5
67D7C9
C6EFE9
E9F9F6
59FF00
82FF00
B8FF75
E3FFCB
F4FFEA
A7469A
B969AE
D3A5CF
EDDBEB
F8F0F9
6B429C
8869AF
B7A5CE
E3DAEB
F3F0F8

Requirements
Must have
• a modern hip feel, somewhat color

```html
<!DOCTYPE html>
<html lang="en">
<head>
<meta charset="utf-8">
<title>Bright Harbor Counseling – Stationery</title>
<link href="https://fonts.googleapis.com/css2?family=Open+Sans:wght@300;400;600&display=swap" rel="stylesheet">
<style>
  :root {
    --backdrop: #e7e7e8;
    --paper: #f7f7f7;
    --ink: #4a4a4c;
    --ink-soft: #6b6b6e;
    --brand-blue: #0677ba;
    --brand-purple: #6b429c;
    --brand-teal: #00bba5;
    --brand-magenta: #a7469a;
    --band-blue: #2f74b5;
    --band-purple: #7b3f8a;
  }
  * { box-sizing: border-box; margin: 0; padding: 0; }
  html, body { width: 1200px; height: 795px; overflow: hidden; }
  body {
    background: var(--backdrop);
    font-family: "Open Sans", Arial, sans-serif;
    color: var(--ink);
    position: relative;
  }

  /* Letterhead */
  .letterhead {
    position: absolute; left: 70px; top: 28px;
    width: 520px; height: 736px;
    background: var(--paper);
    box-shadow: 0 2px 10px rgba(0,0,0,.12);
  }
  .brand {
    position: absolute; right: 118px; top: 52px;
    display: flex; align-items: center; gap: 10px;
  }
  .brand-name {
    font-weight: 300; font-size: 19px; line-height: 1.05;
    color: var(--ink); text-align: right; letter-spacing: .3px;
  }
  .brand-dot {
    width: 30px; height: 30px; border-radius: 50%;
    background: var(--brand-purple);
  }
  .contact {
    position: absolute; right: 34px; top: 150px;
    font-size: 8.5px; font-weight: 600; line-height: 1.45;
    color: var(--ink);
  }
  .contact li { list-style: none; display: flex; align-items: center; gap: 4px; }
  .contact svg { width: 8px; height: 8px; flex: none; }
  .letter {
    position: absolute; left: 48px; top: 132px; width: 300px;
    font-size: 8px; line-height: 1.55; color: var(--ink-soft);
  }
  .salutation { margin-bottom: 8px; }
  .letter p { margin-bottom: 8px; }
  .signoff { margin-top: 14px; }
  .signature {
    display: block; margin-top: 10px; width: 70px; height: 36px;
    background: linear-gradient(90deg, #e4e4e6, #ededee);
    border-radius: 3px;
  }
  .edge-band {
    position: absolute; left: 0; bottom: 0; width: 100%; height: 7px;
    background: linear-gradient(100deg, var(--band-blue) 0 59%, var(--paper) 59% 59.6%, var(--band-purple) 59.6% 100%);
  }

  /* Envelope */
  .envelope {
    position: absolute; left: 625px; top: 262px;
    width: 540px; height: 270px;
    background: var(--paper);
    box-shadow: 0 2px 10px rgba(0,0,0,.12);
  }
  .envelope-flap {
    position: absolute; left: 0; top: 0; width: 100%; height: 100%;
  }
  .envelope .brand { right: 70px; top: 96px; }
  .envelope .brand-name { font-size: 17px; }
  .envelope .brand-dot { width: 26px; height: 26px; }
</style>
</head>
<body>

<section class="letterhead" aria-label="Letterhead">
  <div class="brand">
    <div class="brand-name">Bright Harbor<br>Counseling</div>
    <span class="brand-dot" aria-hidden="true"></span>
  </div>

  <ul class="contact">
    <li>418 Linden Avenue</li>
    <li>Ashford, CA, 90000</li>
    <li>
      <svg viewBox="0 0 10 10" aria-hidden="true"><circle cx="5" cy="5" r="5" fill="var(--brand-blue)"/><path d="M3.3 2.5c.4 1.9 1.7 3.6 3.6 4.6l.6-.9-1.1-.6-.5.5c-.7-.4-1.3-1.1-1.6-1.8l.5-.5-.5-1.1z" fill="#fff"/></svg>
      0400123456
    </li>
    <li>
      <svg viewBox="0 0 10 10" aria-hidden="true"><circle cx="5" cy="5" r="5" fill="var(--brand-magenta)"/><rect x="2.6" y="3.3" width="4.8" height="3.4" fill="none" stroke="#fff" stroke-width=".7"/><path d="M2.6 3.3 5 5.2l2.4-1.9" fill="none" stroke="#fff" stroke-width=".7"/></svg>
      info@brightharbor.com
    </li>
    <li>
      <svg viewBox="0 0 10 10" aria-hidden="true"><circle cx="5" cy="5" r="5" fill="var(--brand-teal)"/><circle cx="5" cy="5" r="2.6" fill="none" stroke="#fff" stroke-width=".7"/><path d="M2.4 5h5.2M5 2.4c-1.4 1.6-1.4 3.6 0 5.2M5 2.4c1.4 1.6 1.4 3.6 0 5.2" fill="none" stroke="#fff" stroke-width=".5"/></svg>
      www.brightharbor.com
    </li>
  </ul>

  <article class="letter">
    <p class="salutation">Dear customer,</p>
    <p>Lorem ipsum dolor sit amet, consectetur adipisicing elit, sed do eiusmod tempor incididunt ut labore et dolore magna aliqua. Ut enim ad minim veniam, quis nostrud exercitation ullamco laboris nisi ut aliquip ex ea commodo consequat. Duis aute irure dolor in reprehenderit in voluptate velit esse cillum dolore eu fugiat nulla pariatur. Excepteur sint occaecat cupidatat non proident, sunt in culpa qui officia deserunt mollit anim id est laborum.</p>
    <p>Lorem ipsum dolor sit amet, consectetur adipisicing elit, sed do eiusmod tempor incididunt ut labore et dolore magna aliqua. Ut enim ad minim veniam, quis nostrud exercitation ullamco laboris nisi ut aliquip ex ea commodo consequat. Duis aute irure dolor in reprehenderit in voluptate velit esse cillum dolore eu fugiat nulla pariatur. Excepteur sint occaecat cupidatat non proident, sunt in culpa qui officia deserunt mollit anim id est laborum.</p>
    <p>Lorem ipsum dolor sit amet, consectetur adipisicing elit, sed do eiusmod tempor incididunt ut labore et dolore magna aliqua. Ut enim ad minim veniam, quis nostrud exercitation ullamco laboris nisi ut aliquip ex ea commodo consequat. Duis aute irure dolor in reprehenderit in voluptate velit esse cillum dolore eu fugiat nulla pariatur. Excepteur sint occaecat cupidatat non proident, sunt in culpa qui officia deserunt mollit anim id est laborum.</p>
    <p>Lorem ipsum dolor sit amet, consectetur adipisicing elit, sed do eiusmod tempor incididunt ut labore et dolore magna aliqua. Ut enim ad minim veniam, quis nostrud exercitation ullamco laboris nisi ut aliquip ex ea commodo consequat. Duis aute irure dolor.</p>
    <p class="signoff">Yours Sincerely,</p>
    <span class="signature" role="img" aria-label="Handwritten signature of the sender"></span>
  </article>

  <div class="edge-band" aria-hidden="true"></div>
</section>

<section class="envelope" aria-label="Envelope">
  <svg class="envelope-flap" viewBox="0 0 540 270" aria-hidden="true">
    <path d="M14 0 V40 Q14 50 24 52 L516 120 Q526 122 526 132 V270" fill="none" stroke="#e2e2e3" stroke-width="1.2"/>
  </svg>
  <div class="brand">
    <div class="brand-name">Bright Harbor<br>Counseling</div>
    <span class="brand-dot" aria-hidden="true"></span>
  </div>
</section>

</body>
</html>
```